Construction Company

Design a clutter free business card, it can be double-sided utilizing the logo for VKM Ltd simple with all relevant contact information.

Please also a letterhead design to function for the purposes of invoicing, all mail requirements, with header to be distinctive while the footer ties page together and incorporates all necessary information.

For now, please use generic / dummy text and when a winner is selected, I will disclose the contact information.

Hi Designers! Please read the updated brief which includes the design of a business card and letterhead. Thank you!

```html
<!DOCTYPE html>
<html lang="en">
<head>
<meta charset="utf-8">
<title>VKM Ltd Business Card</title>
<link href="https://fonts.googleapis.com/css2?family=Arimo:wght@400;700&display=swap" rel="stylesheet">
<style>
  :root {
    --backdrop: #2a2a2a;
    --kraft-light: #dcbb8f;
    --kraft-mid: #c69a68;
    --kraft-dark: #a9794a;
    --ink: #0d0a07;
    --shadow: rgba(0, 0, 0, 0.55);
  }
  * { margin: 0; padding: 0; box-sizing: border-box; }
  html, body {
    width: 1093px;
    height: 1200px;
    overflow: hidden;
    background: var(--backdrop);
    font-family: "Arimo", Arial, sans-serif;
    color: var(--ink);
  }
  .canvas {
    position: relative;
    width: 1093px;
    height: 1200px;
  }
  .card {
    position: absolute;
    left: 264px;
    width: 580px;
    height: 357px;
    background: linear-gradient(135deg, var(--kraft-light) 0%, var(--kraft-mid) 55%, var(--kraft-dark) 100%);
    box-shadow: 3px 3px 4px var(--shadow);
  }
  .card-front { top: 226px; }
  .card-back { top: 620px; }

  .contact-block {
    position: absolute;
    left: 0;
    right: 0;
    top: 68px;
    text-align: center;
  }
  .person-name {
    font-weight: 700;
    font-size: 19px;
    letter-spacing: 0.2px;
    line-height: 22px;
  }
  .person-role {
    font-size: 16px;
    line-height: 20px;
  }
  .divider {
    width: 142px;
    height: 1px;
    background: var(--ink);
    margin: 12px auto 13px;
  }
  .contact-list {
    list-style: none;
    font-size: 16.5px;
    line-height: 21px;
  }
  .contact-label { font-weight: 700; }
  .address {
    font-style: normal;
    font-size: 16.5px;
    line-height: 20px;
    margin-top: 16px;
  }

  .brand {
    position: absolute;
    left: 0;
    right: 0;
    top: 130px;
    display: flex;
    align-items: center;
    justify-content: center;
    gap: 16px;
  }
  .brand-dot {
    width: 34px;
    height: 34px;
    border-radius: 50%;
    background: var(--ink);
  }
  .brand-name {
    font-weight: 700;
    font-size: 72px;
    line-height: 80px;
    letter-spacing: 1px;
  }
</style>
</head>
<body>
<main class="canvas">
  <section class="card card-front" aria-label="Business card front">
    <div class="contact-block">
      <h1 class="person-name">JONATHAN SMITH</h1>
      <p class="person-role">Managing Director</p>
      <div class="divider"></div>
      <ul class="contact-list">
        <li><span class="contact-label">P:</span> 044-123 456 789</li>
        <li><span class="contact-label">M:</span> 044-123 456 789</li>
        <li><span class="contact-label">E:</span> info@webname.com</li>
        <li><span class="contact-label">W:</span> www.websitename.com</li>
      </ul>
      <div class="divider"></div>
      <address class="address">12345, Address Goes Here<br>Country Name, 123456</address>
    </div>
  </section>

  <section class="card card-back" aria-label="Business card back">
    <div class="brand">
      <span class="brand-dot"></span>
      <span class="brand-name">VKM Ltd</span>
    </div>
  </section>
</main>
</body>
</html>
```